Business Card Design

We are a manufacturing and distribution company with most of our customer base being supermarkets. We have established brand guidelines that are attached.

```html
<!DOCTYPE html>
<html lang="en">
<head>
<meta charset="UTF-8">
<title>Corvanta Business Card</title>
<link href="https://fonts.googleapis.com/css2?family=Lato:wght@400;700;900&family=Oswald:wght@500&display=swap" rel="stylesheet">
<style>
  :root {
    --page: #1b1b1c;
    --card: #111112;
    --white: #ffffff;
    --red: #e41b23;
    --blue: #0067b1;
    --rule: #8a8a8a;
  }
  * { box-sizing: border-box; margin: 0; padding: 0; }
  html, body {
    width: 1200px; height: 900px; overflow: hidden;
    background: var(--page);
    font-family: "Lato", sans-serif;
    color: var(--white);
  }
  .canvas {
    position: relative; width: 1200px; height: 900px;
  }
  .card {
    position: absolute; left: 320px; width: 560px; height: 320px;
    background: var(--card);
    box-shadow: 0 10px 30px rgba(0,0,0,.55);
    overflow: hidden;
  }
  .card--front { top: 90px; }
  .card--back { top: 490px; }
  .card__stripe {
    position: absolute; left: 0; right: 0; bottom: 0; height: 9px;
    background: linear-gradient(to right, var(--red) 0 47%, var(--blue) 47% 100%);
  }
  .brand {
    position: absolute; left: 0; right: 0; top: 120px;
    display: flex; align-items: center; justify-content: center; gap: 14px;
  }
  .brand__mark {
    width: 22px; height: 22px; background: var(--red);
  }
  .brand__name {
    font-weight: 900; font-size: 40px; letter-spacing: 4px; color: var(--white);
  }
  .person {
    position: absolute; left: 40px; top: 130px; width: 210px; text-align: right;
  }
  .person__name {
    font-family: "Oswald", sans-serif; font-weight: 500;
    font-size: 30px; line-height: 1; text-transform: uppercase;
  }
  .person__first { color: var(--blue); }
  .person__last { color: var(--red); }
  .person__role { font-size: 15px; margin-top: 6px; }
  .divider {
    position: absolute; left: 272px; top: 125px; width: 1px; height: 80px;
    background: var(--rule);
  }
  .contact {
    position: absolute; left: 292px; top: 132px; list-style: none;
  }
  .contact__item {
    display: flex; align-items: center; gap: 10px;
    font-size: 15px; line-height: 22px; margin-bottom: 2px;
  }
  .contact__icon { width: 14px; height: 14px; flex: none; }
  .address {
    position: absolute; left: 40px; bottom: 34px; font-size: 15px;
  }
</style>
</head>
<body>
<main class="canvas">
  <section class="card card--front">
    <div class="brand">
      <span class="brand__mark"></span>
      <span class="brand__name">CORVANTA</span>
    </div>
    <div class="card__stripe"></div>
  </section>

  <section class="card card--back">
    <div class="person">
      <div class="person__name"><span class="person__first">Daniel</span> <span class="person__last">Hart</span></div>
      <div class="person__role">Managing Director</div>
    </div>
    <div class="divider"></div>
    <ul class="contact">
      <li class="contact__item">
        <svg class="contact__icon" viewBox="0 0 24 24"><path fill="#0067b1" d="M6.6 10.8a15 15 0 0 0 6.6 6.6l2.2-2.2a1 1 0 0 1 1-.25 11.4 11.4 0 0 0 3.6.57 1 1 0 0 1 1 1V20a1 1 0 0 1-1 1A17 17 0 0 1 3 4a1 1 0 0 1 1-1h3.5a1 1 0 0 1 1 1c0 1.25.2 2.45.57 3.57a1 1 0 0 1-.25 1z"/></svg>
        044-555 018 246
      </li>
      <li class="contact__item">
        <svg class="contact__icon" viewBox="0 0 24 24"><rect x="2" y="5" width="20" height="14" fill="none" stroke="#0067b1" stroke-width="2"/><path d="M2 5l10 8 10-8" fill="none" stroke="#0067b1" stroke-width="2"/></svg>
        hello@corvanta.co
      </li>
      <li class="contact__item">
        <svg class="contact__icon" viewBox="0 0 24 24" fill="none" stroke="#0067b1" stroke-width="2"><circle cx="12" cy="12" r="10"/><ellipse cx="12" cy="12" rx="4" ry="10"/><path d="M2 12h20M4 7h16M4 17h16"/></svg>
        www.corvanta.co
      </li>
    </ul>
    <p class="address">18 Mill Road, Harbour City, 20417</p>
    <div class="card__stripe"></div>
  </section>
</main>
</body>
</html>
```